Design eines Hausetiketts für traditionelles Weingut
Zielgruppe
Wir das Familienweingut Brandauer in Gimbsheim/Rheinhessen sind ein traditionelles Weingut das seine Reben selbst kultiviert und die Weine auch selbst ausbaut. Wir haben jeden Schritt in der Weinherstellung selbst in der Hand und vermarkten den Wein dann an unsere Privatkunden. Unsere Kundenstruktur sieht folgendermaßen aus: Wir haben 100% Privatkunden die unseren Wein konsumieren. Da jetzt die nächste Generation in den Weinbaubetrieb einsteigt und auch Ideen hat möchten wir ein Hausetikett einführen. Im Moment haben wir noch sehr viele unterschiedliche Etiketten und kein Hausetikett. Da die Verlagsetiketten immer seltener zu unseren Vorstellungen passen, möchten wir hier auf diesem Wege ein Hausetikett anfertigen lassen. Generell möchten wir unseren Außenauftritt komplett modernisieren. Sie können sich über die Vielfalt in unserem Betrieb unter www.weingut-brandauer-beispiel.de einen Überblick verschaffen. Langfristig gesehen wollen wir aber unsere Weinkarte verkleinern.
Aufgabenstellung
Wir haben uns vor ca. 1,5 Jahren hier auf dieser Website bereits ein Logo designen lassen. Es wäre schön wenn man das Logo bei den Entwürfen für die Etiketten berücksichtigen würde. Das wäre aber KEIN MUSS. Auch wäre es gut wenn man das ,,Wein' bei unserem Namen weglassen könnte.
Das Etikett sollte aus Vorder-und Rückenetikett bestehen und edel wirken. Vorne sollte die Rebsorte und die Geschmacksangabe stehen. Der Rest sollte auf das Rückenetikett.
Das Vorderetikett sollte ein richtiger Eyecatcher sein und im Supermarkt z.B. aus vielen anderen herausstechen. Das wäre ganz wichtig.
Man kann bei den Farben unterscheiden in 3 Konzepte.
Literwein als einsteiger Wein
Dann die Gutsweine und zum Schluss die Lagenweine. Alles Farblich oder im design etwas abgesetzt.

```html
<!DOCTYPE html>
<html lang="de">
<head>
<meta charset="utf-8">
<title>Brandauer – Dornfelder Rotwein 2018</title>
<link rel="stylesheet" href="https://fonts.googleapis.com/css2?family=Marcellus&family=Rochester&family=Saira+Semi+Condensed:wght@500&display=swap">
<style>
  :root {
    --paper: #ffffff;
    --night: #07030d;
    --leaf-deep: #3a0a3a;
    --leaf-mid: #6e1466;
    --leaf-glow: #c21ab8;
    --frame: #8f8a94;
    --text-light: #ffffff;
    --gold: #b08f5c;
    --berry-white: #ffffff;
    --berry-red: #c62a2a;
  }
  * { box-sizing: border-box; margin: 0; padding: 0; }
  html, body {
    width: 960px;
    height: 1200px;
    overflow: hidden;
    background: var(--paper);
  }
  .sheet {
    position: relative;
    width: 960px;
    height: 1200px;
  }
  .label {
    position: absolute;
    left: 0;
    width: 960px;
    height: 590px;
    overflow: hidden;
    background: var(--night);
    color: var(--text-light);
  }
  .label--classic { top: 0; }
  .label--script { top: 596px; }

  .leaf-backdrop {
    position: absolute;
    inset: 0;
    background:
      radial-gradient(ellipse 28% 22% at 18% 58%, rgba(194, 26, 184, 0.75), transparent 70%),
      radial-gradient(ellipse 26% 20% at 90% 52%, rgba(194, 26, 184, 0.6), transparent 70%),
      radial-gradient(ellipse 40% 35% at 55% 40%, rgba(110, 20, 102, 0.9), transparent 75%),
      radial-gradient(ellipse 60% 55% at 50% 60%, var(--leaf-mid), var(--leaf-deep) 70%, var(--night) 100%);
  }
  .frame {
    position: absolute;
    left: 23px;
    top: 30px;
    right: 23px;
    bottom: 27px;
    border: 1.5px solid var(--frame);
  }

  .mark {
    position: absolute;
    left: 50%;
    top: 90px;
    transform: translateX(-50%);
    width: 64px;
    height: 64px;
    border-radius: 50%;
  }
  .label--classic .mark { background: var(--berry-white); }
  .label--script .mark { background: var(--berry-red); }

  .house-name {
    position: absolute;
    left: 0;
    right: 0;
    top: 212px;
    text-align: center;
    font-family: "Marcellus", serif;
    font-weight: 400;
    font-size: 96px;
    line-height: 1;
    letter-spacing: 0;
    white-space: nowrap;
  }
  .label--classic .house-name { color: var(--text-light); }
  .label--script .house-name { color: var(--gold); }

  .variety {
    position: absolute;
    left: 0;
    right: 0;
    text-align: center;
    color: var(--text-light);
    white-space: nowrap;
  }
  .label--classic .variety {
    top: 374px;
    font-family: "Saira Semi Condensed", sans-serif;
    font-weight: 500;
    font-size: 38px;
    line-height: 1;
  }
  .label--script .variety {
    top: 368px;
    font-family: "Rochester", cursive;
    font-size: 48px;
    line-height: 1;
  }

  .vintage {
    position: absolute;
    left: 0;
    right: 0;
    text-align: center;
    color: var(--text-light);
    line-height: 1;
  }
  .label--classic .vintage {
    top: 420px;
    font-family: "Saira Semi Condensed", sans-serif;
    font-weight: 500;
    font-size: 38px;
  }
  .label--script .vintage {
    top: 433px;
    font-family: "Rochester", cursive;
    font-size: 32px;
  }

  .alcohol, .volume {
    position: absolute;
    line-height: 1;
    color: var(--text-light);
    white-space: nowrap;
  }
  .alcohol { left: 32px; }
  .volume { right: 32px; }
  .label--classic .alcohol,
  .label--classic .volume {
    top: 516px;
    font-family: "Saira Semi Condensed", sans-serif;
    font-weight: 500;
    font-size: 36px;
  }
  .label--script .alcohol,
  .label--script .volume {
    top: 516px;
    font-family: "Rochester", cursive;
    font-size: 32px;
  }
  .label--script .alcohol { left: 40px; }

  .lot-number {
    position: absolute;
    left: 0;
    right: 0;
    top: 537px;
    text-align: center;
    font-family: Arial, Helvetica, sans-serif;
    font-size: 16px;
    line-height: 1;
    color: var(--text-light);
    letter-spacing: 0.3px;
  }
</style>
</head>
<body>
<main class="sheet">

  <section class="label label--classic">
    <div class="leaf-backdrop" role="img" aria-label="Hintergrundfoto: magentafarben beleuchtete Weinblätter auf dunklem Grund"></div>
    <div class="frame"></div>
    <span class="mark" aria-hidden="true"></span>
    <h1 class="house-name">BRANDAUER</h1>
    <p class="variety">Dornfelder Rotwein</p>
    <p class="vintage">2018</p>
    <p class="alcohol">12,5 %</p>
    <p class="lot-number">A.P.Nr. 4 912 208 017 19</p>
    <p class="volume">0.75L</p>
  </section>

  <section class="label label--script">
    <div class="leaf-backdrop" role="img" aria-label="Hintergrundfoto: magentafarben beleuchtete Weinblätter auf dunklem Grund"></div>
    <div class="frame"></div>
    <span class="mark" aria-hidden="true"></span>
    <h2 class="house-name">BRANDAUER</h2>
    <p class="variety">Dornfelder Rotwein</p>
    <p class="vintage">2018</p>
    <p class="alcohol">12,5 %</p>
    <p class="lot-number">A.P.Nr. 4 912 208 017 19</p>
    <p class="volume">0.75L</p>
  </section>

</main>
</body>
</html>
```